International IT business needs website revamp.

Velmor Limited would like their current website (www.velmorlimited-example.com) to be revamped/modernized to reflect up-to-date goods and services. Currently, Velmor is offering a conversational AI workflow platform for both enterprise clients and as a DIY solution for SMBs. This platform is called tqFlowbin and allows organizations to automate simple and repetitive workflows to drive their operational efficiency. In addition to the solution offering, Velmor Limited also provides professional IT services. With that said, please use www.velmorlimited-example.com and www.tqflowbin-example.ai for reference of current logos and colourways desired. Furthermore, refer to the attached PDF for a general idea of what to include in the site. The final design should be easy to navigate, clear, concise, and emphasize tqFlowbin as a solution for enterprise clients (while redirecting SMBs to the tqFlowbin website) looking to automate workflow processes/kickstart their digital transformation journey.

```html
<!DOCTYPE html>
<html lang="en">
<head>
<meta charset="utf-8">
<title>Velmor Limited</title>
<link href="https://fonts.googleapis.com/css2?family=Lato:wght@400;700;900&family=Open+Sans:wght@700;800&display=swap" rel="stylesheet">
<style>
:root{
  --blue:#1a7fc1;
  --sky:#6fb8e0;
  --teal:#3db39e;
  --ink:#222;
  --text:#333;
  --grey:#ebebeb;
  --white:#fff;
}
*{box-sizing:border-box;margin:0;padding:0}
html,body{width:1200px;height:2493px;overflow:hidden}
body{position:relative;font-family:'Lato',sans-serif;color:var(--text);background:var(--white)}
.abs{position:absolute}

/* header */
.topbar{left:680px;top:0;width:520px;height:54px;background:var(--sky);clip-path:polygon(0 0,100% 0,100% 100%,22px 100%)}
.topbar-info{left:720px;top:17px;display:flex;gap:26px;font-size:16px;color:#1c2b3a;align-items:center}
.topbar-info span{display:flex;align-items:center;gap:10px}
.topbar-info b{font-weight:700}
.brand{left:75px;top:46px;display:flex;align-items:center;gap:12px}
.brand-mark{width:62px;height:62px;border:4px solid var(--ink)}
.brand-name{font-size:44px;letter-spacing:1px;color:var(--ink);font-weight:400;line-height:1}
.nav{left:411px;top:95px;display:flex;gap:42px;font-size:15px;font-weight:700;color:var(--ink)}
.nav .active{color:var(--blue)}

/* hero */
.hero{left:0;top:141px;width:1200px;height:535px;background:linear-gradient(120deg,#4d6b86 0%,#7f9ab0 45%,#5c6f7e 75%,#3b4650 100%)}
.hero-text{left:0;top:290px;width:1200px;text-align:center;color:var(--white);font-family:'Open Sans',sans-serif}
.hero-title{font-size:64px;font-weight:800;letter-spacing:1px;line-height:1}
.hero-sub{margin-top:12px;font-size:34px;font-weight:800;line-height:41px;letter-spacing:.5px}
.btn{left:520px;top:469px;width:160px;height:46px;background:var(--teal);color:var(--white);font-family:'Open Sans',sans-serif;font-weight:800;font-size:18px;letter-spacing:1.5px;display:flex;align-items:center;justify-content:center}

/* testimonials */
.section-title{width:1200px;text-align:center;font-size:28px;font-weight:700;color:var(--ink);letter-spacing:1px}
.quote{width:500px;text-align:center}
.quote-icon{width:40px;height:40px;border-radius:50%;background:var(--teal);margin:0 auto 24px;display:flex;align-items:center;justify-content:center;color:var(--white);font-family:'Open Sans',sans-serif;font-weight:800;font-size:28px;line-height:1;padding-top:10px}
.quote p{font-size:15px;line-height:27.7px;color:var(--text)}
.quote h4{margin-top:16px;font-size:15px;font-weight:900;color:var(--blue)}
.arrow{top:980px}

/* videos */
.video-band{left:0;top:1178px;width:1200px;height:248px;background:linear-gradient(90deg,#2a8cc7,#3db39e)}
.video-title{top:1228px;color:var(--white)}
.video{top:1300px;width:332px;height:252px;background:var(--white);padding:7px;box-shadow:0 3px 10px rgba(0,0,0,.25)}
.video-fill{width:100%;height:100%;position:relative}
.play{position:absolute;left:50%;top:50%;width:40px;height:40px;margin:-20px 0 0 -20px;border-radius:50%;background:var(--white);display:flex;align-items:center;justify-content:center}

/* clients */
.clients{left:0;top:1626px;width:1200px;height:289px;background:var(--grey)}
.client{top:1772px;width:230px;text-align:center;font-size:40px;font-weight:900;display:flex;align-items:center;justify-content:center;gap:10px}
.client i{display:inline-block;width:28px;height:28px;border-radius:50%}

/* partners */
.partner{top:2032px;width:242px;height:83px;background:var(--white);box-shadow:0 2px 8px rgba(0,0,0,.12);display:flex;align-items:center;justify-content:center;gap:10px;font-size:32px;font-weight:700;color:var(--ink)}
.partner i{display:inline-block;width:26px;height:26px}

/* footer */
footer{color:var(--white)}
.footer{left:0;top:2187px;width:1200px;height:306px;background:var(--blue)}
.foot-brand{left:75px;top:2290px;display:flex;align-items:center;gap:10px}
.foot-brand .brand-mark{width:58px;height:58px;border-color:var(--white)}
.foot-brand .brand-name{color:var(--white);font-size:40px}
.copy{left:75px;top:2370px;font-size:14.5px;line-height:25px}
.foot-col h5{font-size:18px;font-weight:700;letter-spacing:.5px;margin-bottom:6px}
.foot-col li{list-style:none;font-size:14.5px;line-height:29.5px}
.address{font-size:13.5px;line-height:25px}
.social{left:872px;top:2278px;display:flex;gap:22px}
.social i{display:block;width:26px;height:26px;border-radius:50%;border:3px solid var(--white)}
.product{left:872px;top:2345px;display:flex;align-items:center;gap:10px;font-size:34px}
.product i{display:block;width:50px;height:50px;border-radius:50%;background:var(--white)}
</style>
</head>
<body>

<header>
  <div class="abs topbar"></div>
  <div class="abs topbar-info">
    <span>
      <svg width="14" height="14" viewBox="0 0 24 24"><path fill="#1c2b3a" d="M6.6 10.8a15 15 0 0 0 6.6 6.6l2.2-2.2c.3-.3.7-.4 1-.2 1.1.4 2.3.6 3.6.6.6 0 1 .4 1 1V20c0 .6-.4 1-1 1A17 17 0 0 1 3 4c0-.6.4-1 1-1h3.5c.6 0 1 .4 1 1 0 1.3.2 2.5.6 3.6.1.3 0 .7-.2 1z"/></svg>
      <b>+1 (905) 555-0148</b>
    </span>
    <span>
      <svg width="15" height="12" viewBox="0 0 24 18"><path fill="#1c2b3a" d="M0 0h24v3L12 10 0 3zm0 5l12 7 12-7v13H0z"/></svg>
      info@velmorlimited-example.com
    </span>
  </div>
  <div class="abs brand">
    <div class="brand-mark"></div>
    <div class="brand-name">VELMOR</div>
  </div>
  <nav class="abs nav">
    <span class="active">HOME</span><span>COMPANY</span><span>SOLUTIONS</span><span>SERVICES</span><span>REQUEST A DEMO</span><span>CONTACT US</span>
  </nav>
</header>

<section>
  <div class="abs hero" role="img" aria-label="Photo of hands holding a phone with AI interface graphics overlaid"></div>
  <div class="abs hero-text">
    <h1 class="hero-title">VELMOR LIMITED</h1>
    <p class="hero-sub">A CORE TEAM THAT HAS WORKED TOGETHER<br>FOR OVER 15 YEARS.</p>
  </div>
  <div class="abs btn">READ MORE</div>
</section>

<section>
  <h2 class="abs section-title" style="left:0;top:729px">TESTIMONIALS</h2>
  <svg class="abs arrow" style="left:44px" width="16" height="28" viewBox="0 0 16 28"><path d="M14 2L3 14l11 12" stroke="#666" stroke-width="2" fill="none"/></svg>
  <svg class="abs arrow" style="left:1140px" width="16" height="28" viewBox="0 0 16 28"><path d="M2 2l11 12L2 26" stroke="#666" stroke-width="2" fill="none"/></svg>
  <div class="abs quote" style="left:80px;top:801px">
    <div class="quote-icon">&rdquo;</div>
    <p>&ldquo;Naturally, the Northvale Travel Office website receives thousands of visitors a day. As a result, we noticed the need to automate simple and repetitive questions to provide quick, on-demand assistance while maximizing our worker productivity without compromising costs. Thus, we enlisted Velmor Limited and their tqFlowbin solution to accomplish the task. Since launching the Northvale bot in Q4, 2019, we have achieved over 75% of inquiries being automatically answered successfully!&rdquo;</p>
    <h4>NORTHVALE TRAVEL OFFICE</h4>
  </div>
  <div class="abs quote" style="left:621px;top:801px">
    <div class="quote-icon">&rdquo;</div>
    <p>Velmor Limited and their tqFlowbin solution was highly recommended to the Department of Arrivals and Residency (DAR) by Public Access Bureau. The team provided the DAR with the tqFlowbin platform and adequate training for team members to successfully implement the bot. As a result, we were able to deploy 4 bots (two in English and two in French) on the ChatLane channel within 3 weeks! Additionally, we attained close to 80% of inquiries being automatically answered successfully within 4 months!&rdquo;</p>
    <h4>DEPARTMENT OF ARRIVALS AND RESIDENCY</h4>
  </div>
</section>

<section>
  <div class="abs video-band"></div>
  <h2 class="abs section-title video-title" style="left:0">PROMOTIONAL VIDEOS</h2>
  <div class="abs video" style="left:74px">
    <div class="video-fill" role="img" aria-label="Video still of a blue database schema diagram" style="background:linear-gradient(135deg,#1e3f9a,#2f6fd0)">
      <div class="play"><svg width="14" height="16"><path d="M2 1l11 7-11 7z" fill="#222"/></svg></div>
    </div>
  </div>
  <div class="abs video" style="left:435px">
    <div class="video-fill" role="img" aria-label="Video still of a hand touching a digital world map interface" style="background:linear-gradient(135deg,#0f4f8a,#0a1f3a)">
      <div class="play"><svg width="14" height="16"><path d="M2 1l11 7-11 7z" fill="#222"/></svg></div>
    </div>
  </div>
  <div class="abs video" style="left:795px">
    <div class="video-fill" role="img" aria-label="Video still of a business team meeting around a table" style="background:linear-gradient(135deg,#e8e6e2,#b7aa9a)">
      <div class="play"><svg width="14" height="16"><path d="M2 1l11 7-11 7z" fill="#222"/></svg></div>
    </div>
  </div>
</section>

<section>
  <div class="abs clients"></div>
  <h2 class="abs section-title" style="left:0;top:1684px">OUR CLIENTS</h2>
  <div class="abs client" style="left:120px;color:#c8202f"><i style="background:#1e3f8f"></i>Arcvane</div>
  <div class="abs client" style="left:345px;color:#1d5aa6">Tellbrook</div>
  <div class="abs client" style="left:575px;color:#2a1f5c">Paydrift</div>
  <div class="abs client" style="left:820px;color:#111"><i style="background:#f2c200"></i>Onvex</div>
</section>

<section>
  <h2 class="abs section-title" style="left:0;top:1962px">OUR PARTNERS</h2>
  <div class="abs partner" style="left:75px"><i style="background:#ef6a1a"></i>Stemford</div>
  <div class="abs partner" style="left:343px"><i style="background:#2a78d4;border-radius:50%"></i>Tidwell</div>
  <div class="abs partner" style="left:615px"><i style="background:#e8402a;border-radius:50%"></i>Corvel</div>
  <div class="abs partner" style="left:885px"><i style="background:#3a8fd8;border-radius:50%"></i>Relavo</div>
</section>

<footer>
  <div class="abs footer"></div>
  <div class="abs foot-brand">
    <div class="brand-mark"></div>
    <div class="brand-name">VELMOR</div>
  </div>
  <p class="abs copy">Copyright &copy; 2020 Velmor Limited.<br>All rights reserved.</p>
  <div class="abs foot-col" style="left:374px;top:2244px">
    <h5>SITE MAP</h5>
    <ul><li>Home</li><li>Company</li><li>Solutions</li><li>Services</li><li>Request a Demo</li><li>Contact Us</li></ul>
  </div>
  <div class="abs foot-col" style="left:602px;top:2244px">
    <h5>CONTACT US</h5>
    <p style="font-size:14.5px;font-weight:700;line-height:29px">Velmor Ltd.</p>
    <p class="address">72 Lindell Road,<br>Unit 4 &amp; 5 Brookvale, ON<br>Canada K0A 1B2</p>
  </div>
  <div class="abs foot-col" style="left:872px;top:2244px"><h5>FOLLOW US</h5></div>
  <div class="abs social" aria-label="Social links"><i></i><i></i><i></i><i></i><i></i></div>
  <div class="abs product"><i></i>tqFlowbin</div>
</footer>

</body>
</html>
```